Construction material supplies company business card ****

1. Full company name “K T Masonry Works Ltd”
I am after a Business card design for the company as a whole. We are better known in Solomon Islands as “K T Masonry” for short.

We are a building materials supplier of
Ready Mixed Concrete, Bricks and Blocks,
Quarry products- gravel, aggregates, sand etc.
Cement distributor/retailer of reputable brands.
Other prefab concrete products. Culverts, wave breakers, concrete retaining blocks etc.

2. Competitive Advantage over Competition: Quality, efficient, professional, dependable, reliable

3. We want people to feel trust worthy, high quality, strong when they see our brand

5. No preference to color. Maybe more sturdy and corporate. Not fancy.

Industry/Entity Type

CONSTRUCTION SUPPLY

Contact Information for Business Card

Name, Position, office phone mob phone, email

Requirements
Must have
• the company logo
Nice to have
• would like to see a mixture of designs, of with logo only and also with simple graphic designs to bring out the company whilst still have the strong sturdy professional feeling

```html
<!DOCTYPE html>
<html lang="en">
<head>
<meta charset="utf-8">
<title>K T Masonry – Business Card</title>
<link href="https://fonts.googleapis.com/css2?family=Roboto:wght@400;500;700&display=swap" rel="stylesheet">
<style>
  :root {
    --backdrop: #2a2a2a;
    --card: #e3e4e4;
    --card-shade: #d2d4d5;
    --navy: #183f64;
    --navy-soft: #2b4c6e;
    --emboss: #c4c6c7;
    --band-text: #e8eef4;
  }
  * { margin: 0; padding: 0; box-sizing: border-box; }
  html, body {
    width: 1200px; height: 1138px; overflow: hidden;
    background: var(--backdrop);
    font-family: "Roboto", Arial, sans-serif;
  }
  .card {
    position: absolute; left: 290px;
    width: 620px; height: 376px;
    border-radius: 16px;
    background:
      radial-gradient(ellipse at 30% 20%, #eeeff0 0%, transparent 60%),
      radial-gradient(ellipse at 80% 90%, var(--card-shade) 0%, transparent 55%),
      var(--card);
    overflow: hidden;
  }
  .card-front { top: 186px; }
  .card-back { top: 608px; }

  .front-name {
    position: absolute; top: 130px; left: 0; width: 100%;
    text-align: center;
    font-weight: 700; font-size: 62px; letter-spacing: 0.04em;
    color: var(--emboss);
  }
  .front-web {
    position: absolute; top: 328px; left: 0; width: 100%;
    text-align: center;
    font-size: 15px; font-weight: 500; letter-spacing: 0.55em;
    color: var(--navy);
  }

  .brand { position: absolute; left: 36px; top: 54px; display: flex; align-items: center; }
  .brand-mark { width: 66px; height: 66px; background: var(--navy); margin-right: 22px; }
  .brand-name {
    font-weight: 700; font-size: 50px; letter-spacing: 0.03em;
    color: var(--navy); line-height: 1;
  }

  .person { position: absolute; left: 36px; top: 192px; color: var(--navy); }
  .person-name { font-size: 22px; font-weight: 700; }
  .person-role { font-size: 16px; margin-top: 3px; color: var(--navy-soft); }

  .address {
    position: absolute; left: 36px; top: 284px;
    font-size: 16.5px; line-height: 26px; color: var(--navy-soft);
  }

  .contacts { position: absolute; left: 340px; top: 206px; list-style: none; }
  .contacts li {
    display: flex; align-items: center; height: 26px;
    font-size: 16.5px; color: var(--navy-soft);
  }
  .contacts svg { width: 14px; height: 14px; margin-right: 14px; fill: var(--navy); }

  .tagline-band {
    position: absolute; right: 0; bottom: 0; width: 382px; height: 46px;
    background: var(--navy);
    clip-path: polygon(20px 0, 100% 0, 100% 100%, 0 100%);
  }
  .tagline {
    position: absolute; left: 40px; top: 13px;
    font-size: 16px; color: var(--band-text); white-space: nowrap;
  }
</style>
</head>
<body>
  <section class="card card-front">
    <div class="front-name">K T MASONRY</div>
    <div class="front-web">www.ktmasonry.com</div>
  </section>

  <section class="card card-back">
    <div class="brand">
      <div class="brand-mark"></div>
      <div class="brand-name">K T MASONRY</div>
    </div>

    <div class="person">
      <div class="person-name">Daniel Reeves</div>
      <div class="person-role">Managing Director</div>
    </div>

    <div class="address">
      18 Harbour Rd., Ranadi,<br>
      Honiara, SB 00100
    </div>

    <ul class="contacts">
      <li>
        <svg viewBox="0 0 16 16" aria-hidden="true"><path d="M2 5c0-2 2-3 3-3h6c1 0 3 1 3 3l-2 1-1-2H5L4 6 2 5zm2 2h8l2 7H2l2-7zm4 1.5a2 2 0 100 4 2 2 0 000-4z"/></svg>
        000 0000 0000
      </li>
      <li>
        <svg viewBox="0 0 16 16" aria-hidden="true"><path d="M1 3h14v10H1V3zm1.5 1.2L8 8.5l5.5-4.3v-.2h-11v.2zm0 1.6V12h11V5.8L8 10 2.5 5.8z"/></svg>
        daniel@ktmasonry.com
      </li>
      <li>
        <svg viewBox="0 0 16 16" aria-hidden="true"><path d="M8 1a7 7 0 100 14A7 7 0 008 1zm0 1.4c.8.8 1.4 2.1 1.6 3.6H6.4C6.6 4.5 7.2 3.2 8 2.4zM6.3 7.4h3.4c0 .4 0 .8 0 1.2H6.3v-1.2zM2.5 7.4h2.4v1.2H2.5a5.6 5.6 0 010-1.2zm8.6 0h2.4a5.6 5.6 0 010 1.2h-2.4V7.4zM6.4 10h3.2c-.2 1.5-.8 2.8-1.6 3.6-.8-.8-1.4-2.1-1.6-3.6z"/></svg>
        www.ktmasonry.com
      </li>
    </ul>

    <div class="tagline-band">
      <span class="tagline">Efficient, Professional, Dependable, Reliable</span>
    </div>
  </section>
</body>
</html>
```